Business card for law firm

Need business card for new law firm. Think confident, authoritative, conservative, but not stuffy or old-fashioned.

Contact Information for Business Card

Content for card - logo (uploaded), plus the following:

Paul Whitcombe (larger font)
Managing Partner (larger font, but not as large as name)
Level 9, 7 Ferris Lane
Sydney NSW 2000
Main Tel 02 9364 2710
Direct Tel 02 8472 3159
Email paul@qvlegal.com.au
www.qvlegal.com.au

Letterhead design should include logo plus:
Level 9, 7 Ferris Lane
Sydney NSW 2000
Tel 02 8472 3159
www.qvlegal.com.au

```html
<!DOCTYPE html>
<html lang="en">
<head>
<meta charset="utf-8">
<title>Quayvale Lawyers – Business Card</title>
<link rel="stylesheet" href="https://fonts.googleapis.com/css2?family=Jost:wght@400;500;600;700&display=swap">
<style>
  :root {
    --bg: #3a3a3c;
    --navy: #0d1f5c;
    --navy-deep: #0a1a4e;
    --navy-soft: #14296e;
    --ink: #1b1b1f;
    --white: #ffffff;
    --rule: #1e2f6e;
  }
  * { box-sizing: border-box; margin: 0; padding: 0; }
  html, body {
    width: 1200px; height: 1000px; overflow: hidden;
    background: radial-gradient(ellipse at 50% 40%, #4a4a4d 0%, var(--bg) 70%);
    font-family: "Jost", Arial, sans-serif;
  }
  .card {
    position: absolute;
    width: 600px; height: 340px;
    border-radius: 26px;
    overflow: hidden;
    box-shadow: 0 18px 40px rgba(0,0,0,.45);
  }
  /* Back of card */
  .card-back {
    left: 520px; top: 90px;
    background: var(--navy);
  }
  .card-back .backdrop {
    position: absolute; inset: 0;
    background: radial-gradient(ellipse at 18% 30%, var(--navy-soft) 0%, var(--navy) 55%, var(--navy-deep) 100%);
  }
  .card-back .brand {
    position: absolute; left: 250px; top: 130px;
    display: flex; align-items: center; gap: 14px;
    color: var(--white);
  }
  .brand-mark { width: 34px; height: 34px; background: currentColor; }
  .brand-name {
    font-weight: 500; font-size: 30px; letter-spacing: 2px; text-transform: uppercase;
    line-height: 1;
  }
  .card-back .web {
    position: absolute; left: 330px; top: 270px;
    color: var(--white); font-size: 16px; letter-spacing: 1px; font-weight: 500;
  }

  /* Front of card */
  .card-front {
    left: 80px; top: 520px;
    background: var(--white);
  }
  .card-front .band { position: absolute; inset: 0; }
  .card-front .brand {
    position: absolute; left: 36px; top: 36px;
    display: flex; align-items: center; gap: 12px;
    color: var(--navy);
  }
  .card-front .brand .brand-name { color: var(--ink); font-size: 26px; }
  .card-front .brand .brand-mark { width: 30px; height: 30px; background: var(--navy); }
  .person { position: absolute; left: 36px; top: 104px; }
  .person-name { color: var(--navy); font-weight: 700; font-size: 22px; letter-spacing: .5px; line-height: 1.1; }
  .person-role { color: var(--ink); font-size: 15px; margin-top: 2px; }
  .person-rule { position: absolute; left: 36px; top: 158px; width: 250px; height: 1px; background: var(--rule); }
  .phones { position: absolute; left: 36px; top: 172px; font-size: 14px; line-height: 1.45; color: var(--ink); }
  .phones b { color: var(--navy); font-weight: 700; }
  .address { position: absolute; left: 300px; top: 196px; font-size: 14px; color: var(--ink); }
  .address-rule { position: absolute; left: 300px; top: 222px; width: 268px; height: 1px; background: var(--rule); }
  .links { position: absolute; right: 32px; top: 232px; text-align: right; font-size: 14px; line-height: 1.5; color: var(--ink); }
  .links li { list-style: none; display: flex; justify-content: flex-end; align-items: center; gap: 8px; }
  .links .web { font-weight: 600; color: var(--navy); }
  .links svg { width: 13px; height: 13px; }
</style>
</head>
<body>

<section class="card card-back" aria-label="Card back">
  <div class="backdrop" role="img" aria-label="Deep navy background with soft tonal sweep"></div>
  <div class="brand">
    <span class="brand-mark"></span>
    <span class="brand-name">Quayvale Lawyers</span>
  </div>
  <div class="web">www.qvlegal.com.au</div>
</section>

<section class="card card-front" aria-label="Card front">
  <svg class="band" viewBox="0 0 600 340" width="600" height="340" aria-hidden="true">
    <path d="M0 268 H262 Q270 268 276 276 L286 290 Q292 298 302 298 H600 V340 H0 Z" fill="var(--navy)"/>
    <path d="M0 262 H258 Q266 262 272 270" fill="none" stroke="var(--ink)" stroke-width="5"/>
  </svg>

  <div class="brand">
    <span class="brand-mark"></span>
    <span class="brand-name">Quayvale Lawyers</span>
  </div>

  <div class="person">
    <div class="person-name">PAUL WHITCOMBE</div>
    <div class="person-role">Managing Partner</div>
  </div>
  <div class="person-rule"></div>

  <div class="phones">
    <div><b>Main Tel</b> 02 9364 2710</div>
    <div><b>Direct Tel</b> 02 8472 3159</div>
  </div>

  <div class="address">Level 9, 7 Ferris Lane Sydney NSW 2000</div>
  <div class="address-rule"></div>

  <ul class="links">
    <li>paul@qvlegal.com.au
      <svg viewBox="0 0 16 16" aria-hidden="true"><rect x="1" y="3" width="14" height="10" rx="1.5" fill="var(--navy)"/><path d="M2 4 L8 9 L14 4" fill="none" stroke="#fff" stroke-width="1.4"/></svg>
    </li>
    <li><span class="web">www.qvlegal.com.au</span>
      <svg viewBox="0 0 16 16" aria-hidden="true"><circle cx="8" cy="8" r="7" fill="var(--navy)"/><path d="M1 8 H15 M8 1 C4 5 4 11 8 15 M8 1 C12 5 12 11 8 15" fill="none" stroke="#fff" stroke-width="1"/></svg>
    </li>
  </ul>
</section>

</body>
</html>
```